Webdesign Hauskranken- und Tagespflege „Am Lindenhof“
Zielgruppe
Die Hauskranken- und Tagespflege „Am Lindenhof“ in Chemnitz ist ein unabhängiges, privat geführtes Unternehmen im Bereich der ambulanten und teilstationären Kranken- und Seniorenpflege. Seit der Gründung am 1. Mai 2007 stehen wir für eine zuverlässige, individuelle und herzliche Betreuung unserer Klientinnen und Klienten.
Das Team ist ein engagiertes Pflegeteam und auf über 35 qualifizierte Mitarbeiterinnen und Mitarbeiter angewachsen. Gemeinsam setzen wir uns täglich dafür ein, Menschen mit Pflegebedarf eine bestmögliche Versorgung und ein hohes Maß an Lebensqualität zu ermöglichen.
Unsere Firmenphilosophie basiert auf Wertschätzung, Vertrauen und Respekt – sowohl im Umgang mit unseren Klientinnen und Klienten sowie deren Angehörigen als auch innerhalb unseres Teams. Eine persönliche, einfühlsame und fachlich kompetente Betreuung steht für uns an erster Stelle.
Ob Grundpflege oder Behandlungspflege – bei uns sind Sie in guten Händen. Wir begleiten unsere Klientinnen und Klienten mit Fürsorge, Fachkompetenz und Herz und unterstützen sie dabei, ihren Alltag so selbstbestimmt wie möglich zu gestalten.
Gleichzeitig entlasten wir Angehörige, Freunde und Bekannte, indem wir ihnen Sicherheit geben und Freiräume schaffen. So bleibt mehr Zeit für gemeinsame, unbeschwerte Momente mit den Menschen, die ihnen am Herzen liegen.
Unsere Tagespflege bietet Platz für 18 Gäste. Der große Aufenthaltsraum mit offener Küche lädt zum gemütlichen Beisammensein ein. In unserem Ruheraum können sich unsere Gäste bei Bedarf zurückziehen und sich ausruhen, auch Therapien (Logopädie, Ergotherapie, Physiotherapie…) werden darin durchgeführt. Der Aufenthaltsraum ist zum Teil eingerichtet wie eine gemütliche Wohnstube, ihre Einrichtung erinnert an frühere Zeiten. Gemütliche Ruhesessel laden zum Entspannen ein.
Der persönliche Kontakt und das Vertrauen unserer Patientinnen und Patienten bilden dabei st..
Aufgabenstellung
Ziele des Relaunchs:
modernes, freundliches und barrierearmes Design
klare Benutzerführung für Senioren und Angehörige
Hinweis zum Rückrufservice
Notfallnummer dauerhaft sichtbar
schnelle Kontaktaufnahme (Telefon, Rückruf, Kontaktformular)
bessere Auffindbarkeit bei Google (SEO)
Vertrauen durch authentische Bilder, Teamvorstellung und Bewertungen

```html
<!DOCTYPE html>
<html lang="de">
<head>
<meta charset="utf-8">
<title>Hauskranken- und Tagespflege „Am Lindenhof“</title>
<link href="https://fonts.googleapis.com/css2?family=Outfit:wght@300;400;500;600&family=Playfair+Display:ital,wght@0,400;0,500;1,600;1,700&display=swap" rel="stylesheet">
<style>
:root{
  --blue:#1e4f86;
  --yellow:#ffe81a;
  --dark:#2b2c27;
  --page:#f4f2ef;
  --white:#ffffff;
  --ink:#1a1a1a;
  --muted:#5b5b5b;
  --footbar:#e1e0dd;
}
*{margin:0;padding:0;box-sizing:border-box}
html,body{width:1200px;height:3734px;overflow:hidden}
body{background:var(--page);font-family:"Outfit",sans-serif;color:var(--ink);position:relative}
.abs{position:absolute}
.serif{font-family:"Playfair Display",serif}

.topbar{left:0;top:0;width:1200px;height:44px;background:var(--blue);color:#fff;font-size:13px;display:flex;align-items:center;justify-content:flex-end;padding-right:112px;gap:10px}
.topbar .clock{width:26px;height:26px;border-radius:50%;background:#fff;display:flex;align-items:center;justify-content:center}

.nav{left:0;top:44px;width:1200px;height:86px}
.brand{left:96px;top:4px;width:98px;height:98px;border-radius:50%;background:#fff;box-shadow:0 2px 8px rgba(0,0,0,.08);display:flex;align-items:center;justify-content:center;text-align:center;z-index:3}
.brand span{font-size:13px;font-weight:500;color:var(--blue);line-height:1.1}
.menu{left:267px;top:34px;display:flex;gap:24px;font-size:13px;font-weight:400}
.call{left:904px;top:24px;width:189px;height:38px;border-radius:19px;background:var(--blue);color:#fff;font-size:13px;display:flex;align-items:center;justify-content:center;gap:8px}

.hero{left:0;top:130px;width:1200px;height:634px;background:var(--dark);border-radius:36px 36px 0 0;overflow:hidden}
.hero-photo{right:0;top:0;width:620px;height:634px;background:linear-gradient(100deg,var(--dark) 0%,#8a6a2a 30%,#c89a3a 55%,#7f8ea8 78%,#2d4f8a 100%)}
.label{font-size:13px;letter-spacing:2.5px;font-weight:500;display:flex;align-items:center;gap:8px}
.label::before{content:"";width:9px;height:9px;border-radius:50%;background:var(--yellow)}
.hero .label{left:106px;top:140px;color:#fff}
.hero h1{left:106px;top:166px;color:#fff;font-weight:500;font-size:64px;line-height:64px;letter-spacing:-1px}
.hero .kicker{left:106px;top:302px;color:var(--yellow);font-style:italic;font-weight:700;font-size:52px;letter-spacing:-1px}
.hero p{left:106px;top:370px;width:440px;color:#ddd;font-size:16px;line-height:22px;font-weight:300}
.btn{display:flex;align-items:center;justify-content:center;border-radius:22px;font-size:14px}
.btn-yellow{background:var(--yellow);color:var(--ink)}
.hero .b1{left:106px;top:447px;width:208px;height:40px}
.hero .b2{left:323px;top:447px;width:157px;height:40px;border:1.5px solid #fff;color:#fff}

.about{left:0;top:764px;width:1200px;height:1320px;background:var(--page);border-radius:36px 36px 0 0}
.ring{border-radius:50%;border:5px solid var(--yellow);background:var(--page);padding:14px}
.ring .ph{width:100%;height:100%;border-radius:50%}
.about .ring{left:90px;top:58px;width:544px;height:544px}
.badge{width:136px;height:136px;border-radius:50%;background:var(--yellow);border:5px solid #fff;display:flex;align-items:center;justify-content:center;text-align:center;font-size:15px;font-weight:500;color:var(--blue);line-height:1.15}
.about .badge{left:494px;top:443px}
.about .label{left:693px;top:94px;color:var(--ink)}
.about h2{left:693px;top:122px;font-weight:400;font-size:50px;line-height:51px;letter-spacing:-.5px;color:var(--ink)}
.about .sub{left:693px;top:281px;color:var(--blue);font-style:italic;font-weight:600;font-size:31px}
.about p{left:693px;top:345px;width:436px;font-size:12.5px;line-height:20.5px;color:var(--muted);font-weight:300}

.card{top:678px;width:482px;height:548px;background:#fff;border-radius:26px;padding:14px}
.card .ph{height:352px;border-radius:18px}
.card h3{text-align:center;font-weight:400;font-size:32px;margin-top:28px}
.card .btn{margin-top:24px;height:64px;border-radius:32px;font-size:21px}
.c1{left:106px}.c2{left:611px}

.mission{left:0;top:2084px;width:1200px;height:720px;background:var(--blue);border-radius:36px 36px 0 0;color:#fff}
.mission .label{left:84px;top:74px;color:#fff}
.mission h2{left:84px;top:102px;font-weight:400;font-size:54px;line-height:54px}
.mission .sub{left:84px;top:214px;color:var(--yellow);font-style:italic;font-weight:600;font-size:30px;line-height:34px;width:420px}
.mission p{left:84px;width:396px;font-size:12.5px;line-height:20.5px;font-weight:300;color:#dfe7f2}
.mission .p1{top:310px}.mission .p2{top:386px}
.mission .btn{left:84px;top:536px;width:229px;height:46px;font-size:19px;border-radius:23px}
.mission .ring{left:568px;top:53px;width:544px;height:544px;background:var(--blue)}
.mission .badge{left:564px;top:2526px}

.info{left:0;top:2770px;width:1200px;height:200px;background:var(--yellow)}
.info-item{top:40px;display:flex;align-items:center;gap:16px;font-size:19px;font-weight:500;line-height:25px;color:var(--ink)}
.ic{width:72px;height:72px;border-radius:50%;background:var(--blue);border:5px solid #fff;display:flex;align-items:center;justify-content:center;flex:none}

.mapwrap{left:0;top:2934px;width:1200px;height:800px;background:var(--page);border-radius:36px 36px 0 0}
.map{left:106px;top:80px;width:987px;height:493px;background:#fff;border-radius:24px;padding:8px;box-shadow:0 6px 24px rgba(0,0,0,.05)}
.map .ph{width:100%;height:100%;border-radius:18px;background:linear-gradient(90deg,#e9ecef 0%,#eef0f2 65%,#d5f0dc 100%)}
.copy{left:0;top:655px;width:1200px;text-align:center;font-size:24px}
.footbar{left:0;top:709px;width:1200px;height:35px;background:var(--footbar);display:flex;justify-content:center;align-items:center;gap:34px;font-size:13px}
</style>
</head>
<body>

<div class="abs topbar">
  <span class="clock"><svg width="14" height="14" viewBox="0 0 24 24"><circle cx="12" cy="12" r="10" fill="#1e4f86"/><path d="M12 6v6l4 2" stroke="#fff" stroke-width="2.4" fill="none" stroke-linecap="round"/></svg></span>
  <span>Mo - Do: 9:00 - 15:00 Uhr | Fr: 9:00 - 14:00 Uhr | und nach Vereinbarung</span>
</div>

<header class="abs nav">
  <div class="abs brand"><span>Am<br>Lindenhof</span></div>
  <nav class="abs menu"><span>Über uns</span><span>Team</span><span>Pflegeleitbild</span><span>Partner</span><span>Hauskrankenpflege</span><span>Tagespflege</span><span>Aktuelles</span></nav>
  <div class="abs call"><svg width="14" height="14" viewBox="0 0 24 24"><path fill="#fff" d="M6.6 10.8a15 15 0 0 0 6.6 6.6l2.2-2.2c.3-.3.7-.4 1-.2 1.1.4 2.3.6 3.6.6.6 0 1 .4 1 1V20c0 .6-.4 1-1 1A17 17 0 0 1 3 4c0-.6.4-1 1-1h3.5c.6 0 1 .4 1 1 0 1.3.2 2.5.6 3.6.1.3 0 .7-.2 1z"/></svg>+49 371 - 555 - 0148</div>
</header>

<section class="abs hero">
  <div class="abs hero-photo" role="img" aria-label="Foto: Pflegerin umarmt eine lächelnde ältere Dame"></div>
  <div class="abs label">AM-LINDENHOF</div>
  <h1 class="abs serif">Helft denen,<br>die Hilfe brauchen.</h1>
  <div class="abs kicker serif">Mitarbeiter gesucht!!!</div>
  <p class="abs">Ambulante Pflege und Tagespflege „Am Lindenhof“ in Chemnitz – persönlich, kompetent und menschlich.</p>
  <div class="abs btn btn-yellow b1">Jetzt Kontakt aufnehmen</div>
  <div class="abs btn b2">Rückruf anfordern</div>
</section>

<section class="abs about">
  <div class="abs ring"><div class="ph" role="img" aria-label="Foto: ältere Dame mit junger Pflegerin" style="background:linear-gradient(135deg,#e8e2da,#b9a38e 55%,#6f6a66)"></div></div>
  <div class="abs badge">Am<br>Lindenhof</div>
  <div class="abs label">AM-LINDENHOF</div>
  <h2 class="abs serif">Hauskranken-<br>und Tagespflege<br>“Am Lindenhof”</h2>
  <div class="abs sub serif">Ihr Pflegeteam aus Chemnitz</div>
  <p class="abs">Lassen Sie Ihren Alltag durch unsere Bezugspflege erleichtern. Wir stehen Ihnen mit helfender Hand zur Seite. Jeder Mensch hat den Wunsch mit Respekt und liebevoller Zuwendung versorgt zu werden. Das Ziel unserer Einrichtung ist Sie oder Ihren Angehörigen bei Pflege und Bewältigung des Alltags, in dieser Weise zu unterstützen. Somit kann eine selbstbestimmte Lebensführung und ein aktive Teilnahme an der Gesellschaft ermöglicht werden. Ihre persönlichen Bedürfnisse, religiöse Gewohnheiten und individuellen Wünsche stehen für unseren Pflegedienst ganz im Vordergrund. Pflegebedürftigkeit soll nicht zu einer Passivität führen, durch unsere Pflege möchten wir aktiv an der Verbesserung bzw. Erhaltung Ihrer Lebensqualität mitwirken.</p>

  <article class="abs card c1">
    <div class="ph" role="img" aria-label="Foto: Pflegerin beschäftigt sich mit Senioren am Tisch" style="background:linear-gradient(135deg,#d9d4cc,#8fa6b3 50%,#5a6e7a)"></div>
    <h3>Hauskrankenpflege</h3>
    <div class="btn btn-yellow">Mehr dazu erfahren</div>
  </article>
  <article class="abs card c2">
    <div class="ph" role="img" aria-label="Foto: lachende Seniorin in der Tagespflege" style="background:linear-gradient(135deg,#4a4f55,#9a9ca0 50%,#3b3d41)"></div>
    <h3>Tagespflege</h3>
    <div class="btn btn-yellow">Mehr dazu erfahren</div>
  </article>
</section>

<section class="abs mission">
  <div class="abs label">AM-LINDENHOF</div>
  <h2 class="abs serif">Unser<br>Pflegeleitbild</h2>
  <div class="abs sub serif">wir, die hauskranken- und tagespflege „am lindenhof“,</div>
  <p class="abs p1">Wir, die Hauskranken- und Tagespflege „Am Lindenhof“, sind ein unabhängiges, privatrechtliches Unternehmen der ambulanten bzw. teilstationären Kranken- und Seniorenpflege.</p>
  <p class="abs p2">Jeder Mensch hat den Wunsch mit Respekt und liebevoller Zuwendung versorgt zu werden. Das Ziel unserer Einrichtung ist unsere Betreuten bzw. Ihre Angehörigen bei der Pflege und Bewältigung des Alltags im häuslichen Umfeld, in dieser Weise zu unterstützen. Somit kann eine Lebensführung und eine aktive Teilnahme an der Gesellschaft ermöglicht werden.</p>
  <div class="abs btn btn-yellow">Mehr dazu erfahren</div>
  <div class="abs ring"><div class="ph" role="img" aria-label="Foto: Seniorin wird liebevoll frisiert" style="background:linear-gradient(135deg,#f1efec,#d8cdb8 50%,#7a8aa6)"></div></div>
</section>
<div class="abs badge" style="left:564px;top:2526px">Am<br>Lindenhof</div>

<section class="abs info">
  <div class="abs info-item" style="left:91px"><span class="ic"><svg width="30" height="30" viewBox="0 0 24 24"><path fill="#fff" d="M6.6 10.8a15 15 0 0 0 6.6 6.6l2.2-2.2c.3-.3.7-.4 1-.2 1.1.4 2.3.6 3.6.6.6 0 1 .4 1 1V20c0 .6-.4 1-1 1A17 17 0 0 1 3 4c0-.6.4-1 1-1h3.5c.6 0 1 .4 1 1 0 1.3.2 2.5.6 3.6.1.3 0 .7-.2 1z"/></svg></span><span>24h-Hotline<br>0371 / 4700200</span></div>
  <div class="abs info-item" style="left:413px"><span class="ic"><svg width="28" height="28" viewBox="0 0 24 24"><path fill="#fff" d="M12 2a7 7 0 0 0-7 7c0 5 7 13 7 13s7-8 7-13a7 7 0 0 0-7-7zm0 9.5A2.5 2.5 0 1 1 12 6.5a2.5 2.5 0 0 1 0 5z"/></svg></span><span>Lindenallee 12<br>09126 Chemnitz</span></div>
  <div class="abs info-item" style="left:747px;top:28px"><span class="ic"><svg width="30" height="30" viewBox="0 0 24 24"><circle cx="12" cy="12" r="9.5" fill="none" stroke="#fff" stroke-width="2.4"/><path d="M12 7v5l3 2" stroke="#fff" stroke-width="2.4" fill="none" stroke-linecap="round"/></svg></span><span>Mo - Do: 9:00 - 15:00 Uhr<br>Fr: 9:00 - 14:00 Uhr<br>und nach Vereinbarung</span></div>
</section>

<section class="abs mapwrap">
  <div class="abs map"><div class="ph" role="img" aria-label="Stadtplan von Chemnitz mit Standort der Pflegeeinrichtung"></div></div>
  <div class="abs copy">© 2026 Hauskranken- und Tagespflege „Am Lindenhof“</div>
  <nav class="abs footbar"><span>Kontakt</span><span>Datenschutz</span><span>Impressum</span><span>Erklärung zur Barrierefreiheit</span></nav>
</section>

</body>
</html>
```